Business Card Design for BrightvaleMedia.com

--I need a business card design for my company BrightvaleMedia.com

I have attached my logo...I want the brightvale media logo on the front of the business card, and then I want The Quillstone Chief on the back of it with my information.

I would like to see a light colored background as well as a dark colored background

FRONT:
BRIGHTVALE MEDIA LOGO
248 N. Larkmoor
3rd Floor
San Diego CA 92173
www.BrightvaleMedia.com

Advanced Website & App Development
Websites, Apps, Online Voucher Systems

Leading Edge Marketing Services
SMS, VB, SMM, SEM,

BACK:
QUILLSTONE CHIEF LOGO
Dorian Pelletta
The Quillstone Chief
Call Or Text: 619-555-0148
Dorian@QuillstoneChief.example
www.QuillstoneChief.example

Target Market(s)

small business owners

Industry/Entity Type

Business Consultant

Contact Information for Business Card

FRONT:
BRIGHTVALE MEDIA LOGO
248 N. Larkmoor
3rd Floor
San Diego CA 92173
www.BrightvaleMedia.com

SMS, VB, SMM, SEM,

BACK:
QUILLSTONE CHIEF LOGO
Dorian Pelletta
The Quillstone Chief
Dorian@QuillstoneChief.example
www.QuillstoneChief.example

Requirements
Must have
• add this quote on it somewhere, anywhere,preferrably on back
• "The Fastest Way To Success Is To Take Action”
• — Dorian Pelletta, Quillstone Chief
Nice to have
• open
Should not have
• red

```html
<!DOCTYPE html>
<html lang="en">
<head>
<meta charset="utf-8">
<title>Brightvale Media Business Card</title>
<link href="https://fonts.googleapis.com/css2?family=Montserrat:wght@400;500;600;700&display=swap" rel="stylesheet">
<style>
  :root {
    --backdrop: #2e2f31;
    --card-grey: #6b6c6e;
    --card-white: #ffffff;
    --brand-blue: #1b6fb3;
    --text-grey: #6f7073;
    --band-grey: #808184;
    --rule-grey: #8a8b8e;
    --white: #ffffff;
  }
  html, body {
    margin: 0;
    padding: 0;
    width: 1200px;
    height: 900px;
    overflow: hidden;
    background: var(--backdrop);
    font-family: "Montserrat", sans-serif;
  }
  .canvas {
    position: relative;
    width: 1200px;
    height: 900px;
  }
  .card {
    position: absolute;
    width: 600px;
    height: 343px;
    border-radius: 26px;
    overflow: hidden;
    box-sizing: border-box;
  }

  /* Front: company card */
  .card-front {
    left: 70px;
    top: 110px;
    background: var(--card-grey);
    color: var(--white);
  }
  .front-brand {
    position: absolute;
    top: 50px;
    left: 0;
    right: 0;
    text-align: center;
    font-size: 44px;
    font-weight: 500;
    letter-spacing: 4px;
    color: var(--white);
  }
  .front-address {
    position: absolute;
    top: 138px;
    left: 0;
    right: 0;
    text-align: center;
    font-size: 14px;
    line-height: 20px;
    font-weight: 400;
  }
  .front-address strong { font-weight: 700; }
  .front-services {
    position: absolute;
    left: 42px;
    bottom: 38px;
    font-size: 14px;
    line-height: 19px;
  }
  .front-services .service-head { font-weight: 700; }
  .front-strip {
    position: absolute;
    left: 0;
    bottom: 0;
    width: 372px;
    height: 10px;
    background: var(--white);
  }
  .front-strip-notch {
    position: absolute;
    left: 372px;
    bottom: 0;
    width: 4px;
    height: 22px;
    background: var(--white);
  }

  /* Back: personal card */
  .card-back {
    left: 530px;
    top: 430px;
    background: var(--card-white);
  }
  .name-block {
    position: absolute;
    right: 40px;
    top: 36px;
    text-align: right;
  }
  .person-name {
    font-size: 24px;
    font-weight: 600;
    color: var(--brand-blue);
    line-height: 30px;
  }
  .person-title {
    font-size: 13px;
    line-height: 16px;
    color: var(--text-grey);
  }
  .name-tab {
    position: absolute;
    right: 0;
    top: 36px;
    width: 22px;
    height: 40px;
    background: var(--brand-blue);
  }
  .name-rule {
    position: absolute;
    right: 40px;
    top: 90px;
    width: 230px;
    height: 2px;
    background: var(--rule-grey);
  }
  .back-brand {
    position: absolute;
    left: 38px;
    top: 122px;
    font-size: 32px;
    line-height: 40px;
    font-weight: 600;
    letter-spacing: 2px;
    color: var(--brand-blue);
  }
  .contact-rule {
    position: absolute;
    left: 36px;
    top: 226px;
    width: 200px;
    height: 2px;
    background: var(--rule-grey);
  }
  .contact-list {
    position: absolute;
    left: 36px;
    top: 236px;
    margin: 0;
    padding: 0;
    list-style: none;
    font-size: 14px;
    line-height: 21px;
    color: var(--text-grey);
  }
  .contact-list li { display: flex; align-items: center; gap: 8px; }
  .contact-list svg { width: 11px; height: 11px; fill: var(--brand-blue); }
  .contact-list strong { color: var(--brand-blue); font-weight: 700; }
  .quote {
    position: absolute;
    right: 36px;
    top: 307px;
    font-size: 12px;
    line-height: 16px;
    letter-spacing: 0.5px;
    text-transform: uppercase;
    color: var(--text-grey);
    white-space: nowrap;
  }
  .band-blue {
    position: absolute;
    left: 0;
    bottom: 0;
    width: 360px;
    height: 12px;
    background: var(--brand-blue);
  }
  .band-grey {
    position: absolute;
    left: 360px;
    right: 0;
    bottom: 0;
    height: 12px;
    background: var(--band-grey);
  }
</style>
</head>
<body>
<div class="canvas">

  <section class="card card-front">
    <div class="front-brand">BRIGHTVALE MEDIA</div>
    <div class="front-address">
      248 N. Larkmoor<br>
      3rd Floor<br>
      San Diego CA 92173<br>
      www.<strong>BrightvaleMedia</strong>.com
    </div>
    <div class="front-services">
      <div>Advanced Website &amp; App Development</div>
      <div>Websites, Apps, Online Voucher Systems</div>
      <div class="service-head">LEADING EDGE MARKETING SERVICES</div>
      <div class="service-head">SMS, VB, SMM, SEM,</div>
    </div>
    <div class="front-strip"></div>
    <div class="front-strip-notch"></div>
  </section>

  <section class="card card-back">
    <div class="name-block">
      <div class="person-name">Dorian Pelletta</div>
      <div class="person-title">CEO</div>
    </div>
    <div class="name-tab"></div>
    <div class="name-rule"></div>

    <div class="back-brand">QUILLSTONE CHIEF</div>

    <div class="contact-rule"></div>
    <ul class="contact-list">
      <li>
        <svg viewBox="0 0 24 24" aria-hidden="true"><path d="M6.6 10.8a15.1 15.1 0 0 0 6.6 6.6l2.2-2.2a1 1 0 0 1 1-.25 11.4 11.4 0 0 0 3.6.57 1 1 0 0 1 1 1V20a1 1 0 0 1-1 1A17 17 0 0 1 3 4a1 1 0 0 1 1-1h3.5a1 1 0 0 1 1 1c0 1.25.2 2.45.57 3.57a1 1 0 0 1-.25 1z"/></svg>
        619-555-0148
      </li>
      <li>
        <svg viewBox="0 0 24 24" aria-hidden="true"><path d="M2 5h20v14H2zm2 2v.5l8 5 8-5V7zm0 3v7h16v-7l-8 5z"/></svg>
        Dorian@QuillstoneChief.example
      </li>
      <li>
        <svg viewBox="0 0 24 24" aria-hidden="true"><circle cx="12" cy="12" r="10"/></svg>
        <span>www.<strong>QuillstoneChief</strong>.example</span>
      </li>
    </ul>

    <div class="quote">The fastest way to success is to take action</div>
    <div class="band-blue"></div>
    <div class="band-grey"></div>
  </section>

</div>
</body>
</html>
```